Website for Reiki and Wellness Courses

I teach online courses in Reiki and wellness/self-development and am needing a new website.

The focus of the website will be to provide descriptions of the courses as well as include a blog and pages where students in my courses will visit for additional information.

Note: courses are NOT hosted on this site.
The focus of this website will be to encourage viewers to enroll in courses as well as opt in to the email list.

I will upload copy soon. My old website is: http://brightfernstudies.example. Please do not use existing logo.

Target Market(s)

Alternative health, wellness, spirituality, personal development. Males and females of all ages seeking to improve their health and life.

Industry/Entity Type

Health And Wellness

Logo Text

No text (please do not use existing logo)

Coding

Coded - Design and coding required

Number of Pages Required

5+ page

Requirements
Must have
• 1. Home page
• 2. About page
• 3. Courses page that outlines courses (there are currently 6 courses with 1 coming soon)
• 4. Individual course page (maybe a template that I can adjust color and pictures for with each course)
• 5. Blog
• 6. Student Area that outlines all Student Areas
• 7. Individual Student Area page (maybe a template that I can adjust color and pictures for with each course)
• 8. Shop page (note: items will not currently be purchased through website - it will be a link to quillmarket for a book).
• 9. Student thank-you page (maybe a template that I can adjust color and pictures for with each course) this is the page students are directed to at end of course with vouchers for other courses.
• Opt-in for the home page, course pages, blog and thank-you pages
Nice to have
• I would like the design to be calm, clean and soothing. Ideally visitors feel relaxed when viewing the site and are encouraged to explore the courses, subscribe to the email list and purchase a product.
• ~ Testimonials page
• ~ Contact page
• I tend to gravitate towards blues, greys and purples as well as monochromatic color schemes.
Should not have
• Contact form on home page
• phone number on home page
• location/physical address
• dates for blog posts

```html
<!DOCTYPE html>
<html lang="en">
<head>
<meta charset="utf-8">
<title>Bright Fern Studies</title>
<link rel="stylesheet" href="https://fonts.googleapis.com/css2?family=Lato:wght@400;700&family=Open+Sans:wght@400;600;700&display=swap">
<style>
:root{
  --navy:#1c2a3e;
  --navy-deep:#101a28;
  --orange:#f28a1e;
  --orange-dark:#d96f0a;
  --sky:#1fb4e8;
  --ink:#2b2b2b;
  --grey:#555;
  --rule:#cfcfcf;
  --white:#fff;
  --teal-dark:#14262c;
  --footer:#2c2b26;
  --date-red:#d62a1e;
}
*{box-sizing:border-box;margin:0;padding:0}
html,body{width:1200px;height:2353px;overflow:hidden}
body{position:relative;background:var(--white);font-family:"Open Sans",Arial,sans-serif;color:var(--ink)}
.abs{position:absolute}
a{color:inherit;text-decoration:none}

/* header */
.site-header{left:0;top:0;width:1200px;height:100px;background:linear-gradient(180deg,#2a3a52,var(--navy-deep))}
.brand{left:95px;top:22px;display:flex;align-items:center;gap:10px}
.brand-dot{width:40px;height:40px;border-radius:50%;background:var(--orange)}
.brand-name{font-family:"Open Sans",sans-serif;font-weight:700;font-size:25px;color:var(--orange);line-height:1.05;width:200px}
.follow{right:96px;top:12px;display:flex;align-items:center;gap:9px;color:var(--white);font-size:12px;font-weight:600}
.follow span{margin-right:6px}
.social{width:31px;height:31px;border-radius:50%;border:2px solid var(--white)}
.social.s1{background:#3b5a9a}.social.s2{background:#1a78b5}.social.s3{background:#2aa9e0}.social.s4{background:#d9432f}
.main-nav{right:80px;top:68px;display:flex;font-size:12.5px;color:var(--white);font-weight:600}
.main-nav a{padding:0 26px;border-left:1px solid rgba(255,255,255,.7);line-height:20px}
.main-nav a:first-child{border-left:0}
.main-nav a.active{color:var(--orange)}

/* hero */
.hero{left:0;top:100px;width:1200px;height:471px;background:radial-gradient(ellipse at 30% 60%,#c9d6ea 0%,#7d98c3 35%,#3c5f99 70%,#1e3b6e 100%)}
.hero-text{right:99px;top:121px;width:500px;text-align:right;font-family:"Lato",sans-serif;font-size:27px;line-height:33px;color:var(--white)}

/* opt-in */
.optin{left:0;top:571px;width:1200px;height:261px;background:linear-gradient(90deg,#0f1a12,#2c3d2e 30%,#24332a 70%,#0d1610);text-align:center;color:var(--white)}
.optin h2{position:absolute;top:20px;width:100%;font-family:"Lato",sans-serif;font-weight:400;font-size:27px}
.divider-small{position:absolute;left:450px;top:70px;width:300px;height:1px;background:rgba(255,255,255,.5)}
.divider-small::after{content:"";position:absolute;left:141px;top:-9px;width:18px;height:18px;border-radius:50%;border:1.5px solid var(--white);background:#24332a}
.optin p{position:absolute;left:165px;top:98px;width:870px;font-size:12.5px;line-height:19px}
.field{position:absolute;top:149px;width:206px;height:34px;background:var(--white);border:2px solid var(--orange);color:#333;font-size:11.5px;text-align:left;padding:9px 8px}
.btn-orange{position:absolute;left:520px;top:199px;width:160px;height:37px;border-radius:7px;background:var(--orange);border:1px solid var(--orange-dark);color:#222;font-weight:700;font-size:14px;line-height:35px}

/* section titles */
.sec-title{width:1200px;text-align:center;font-family:"Open Sans",sans-serif;font-size:27px;font-weight:400;color:var(--orange)}
.sec-title em{font-style:normal;color:var(--sky)}
.sec-rule{left:97px;width:1005px;height:1px;background:var(--rule)}
.sec-rule::after{content:"";position:absolute;left:492px;top:-10px;width:20px;height:20px;border-radius:50%;border:1.5px solid var(--orange);background:inherit}

/* courses */
.course{width:240px;text-align:center}
.course h3{font-weight:400;font-size:17px;line-height:21px;color:#333;height:44px}
.course-img{width:215px;height:182px;margin:7px auto 0;border:4px solid #fff;box-shadow:0 2px 6px rgba(0,0,0,.35)}
.course-img.selected{border-color:var(--sky)}
.course p{font-size:12.5px;line-height:17px;color:#333;margin:22px auto 0;width:210px;height:52px}
.course .more{display:inline-block;margin-top:12px;font-size:12.5px;text-decoration:underline;color:#333}
.course .more.hi{color:var(--sky);font-weight:700}

/* welcome */
.welcome{left:0;top:1364px;width:1200px;height:429px;background:radial-gradient(ellipse at 50% 80%,#3e5056 0%,#24363c 45%,var(--teal-dark) 100%)}
.welcome .sec-rule{background:rgba(255,255,255,.35)}
.welcome .sec-rule::after{background:#243539}
.welcome p{position:absolute;left:110px;top:148px;width:980px;text-align:center;color:#e8e8e8;font-family:"Lato",sans-serif;font-size:13px;line-height:24.5px}
.btn-dark{left:542px;top:261px;width:116px;height:35px;border-radius:7px;background:#000;border:1px solid #aaa;color:var(--white);font-size:14px;text-align:center;line-height:33px}
.feature{top:324px;width:240px;height:60px;border:1px solid rgba(255,255,255,.45);background:rgba(60,75,80,.55);color:var(--white);font-size:14px;line-height:19px;display:flex;align-items:center}
.feature .ico{width:52px;height:100%;border-right:1px solid rgba(255,255,255,.35);display:flex;align-items:center;justify-content:center;margin-right:14px}
.feature .ico span{width:26px;height:26px;border-radius:50%;border:1.5px solid var(--white)}

/* blog + testimonials */
.col-title{font-family:"Open Sans",sans-serif;font-size:27px;font-weight:400;color:#222}
.col-title em{font-style:normal;color:var(--orange)}
.dotrule{height:0;border-top:1px dotted #888}
.arrows{font-size:16px;color:#333;letter-spacing:1px}
.post{left:100px;width:505px;display:flex;gap:18px}
.post-img{width:102px;height:86px;flex:none;border:1px solid #ccc}
.post h4{font-size:12.5px;font-weight:700;color:#222;line-height:16px;white-space:nowrap}
.post .date{color:var(--date-red);font-size:12.5px;margin:6px 0 4px;line-height:16px}
.post p{font-size:12.5px;line-height:17px;color:#333}
.post p b{font-weight:700}
.avatar{left:648px;top:1914px;width:86px;height:86px;border-radius:50%;background:linear-gradient(#a9a39b,#6d6760);border:3px solid #ddd}
.t-name{left:756px;top:1937px;font-size:13px;color:#555;text-transform:uppercase}
.t-role{left:756px;top:1957px;font-size:12.5px;color:var(--date-red)}
.quote{left:650px;top:2025px;width:450px;font-family:"Lato",sans-serif;font-size:12.5px;line-height:24px;color:#333}
.quote::before{content:"\201C";color:#e8a9a0;font-size:30px;line-height:0;vertical-align:-10px;margin-right:8px}

/* footer */
.site-footer{left:0;top:2172px;width:1200px;height:181px;background:linear-gradient(90deg,#1a1915,var(--footer) 30%,#3a382f 100%);color:var(--white);text-align:center}
.foot-nav{position:absolute;left:0;top:22px;width:1200px;display:flex;justify-content:center;font-size:14px}
.foot-nav a{padding:0 20px;border-left:1px solid rgba(255,255,255,.7);line-height:18px}
.foot-nav a:first-child{border-left:0}
.foot-nav a.active{color:var(--orange);font-weight:700}
.accept{position:absolute;left:0;top:62px;width:1200px;display:flex;justify-content:center;align-items:center;gap:6px;font-size:12px}
.accept span{margin-right:8px}
.card{width:38px;height:25px;border-radius:4px;border:1px solid #fff}
.foot-brand{position:absolute;left:0;top:95px;width:1200px;display:flex;justify-content:center;align-items:center;gap:8px}
.foot-brand .brand-dot{width:28px;height:28px}
.foot-brand .brand-name{font-size:17px;width:auto;text-align:left}
.copy{position:absolute;top:150px;width:1200px;font-size:11.5px}
</style>
</head>
<body>

<header class="site-header abs">
  <div class="brand abs"><span class="brand-dot"></span><span class="brand-name">BRIGHT FERN STUDIES</span></div>
  <div class="follow abs"><span>Follow Us On</span><i class="social s1"></i><i class="social s2"></i><i class="social s3"></i><i class="social s4"></i></div>
  <nav class="main-nav abs">
    <a class="active" href="#">Home</a><a href="#">About Us</a><a href="#">Online Courses</a><a href="#">Student Areas</a><a href="#">Testimonials</a><a href="#">Contact Us</a>
  </nav>
</header>

<section class="hero abs" role="img" aria-label="Photo of stacked pebbles and a white water lily on misty blue water">
  <p class="hero-text abs">Lorem ipsum dolor sit amet, consectet adipiscing elit, sed diam nonummy d tincidunt ut laoreet dolore magna aliquam erat volutpat facilisi</p>
</section>

<section class="optin abs" role="img" aria-label="Photo of a dark green forest canopy">
  <h2>Stay Inspired</h2>
  <div class="divider-small"></div>
  <p>Receive information and articles each month to keep you feeling inspired. As a thank-you, you will also receive access to soothing music you can download for use in your Reiki sessions and meditation.</p>
  <div class="field" style="left:268px">First Name</div>
  <div class="field" style="left:498px">Last Name</div>
  <div class="field" style="left:729px">Email Address</div>
  <div class="btn-orange">Yes-Count Me In</div>
</section>

<h2 class="sec-title abs" style="left:0;top:880px">Our Bright Fern <em>Studies</em></h2>
<div class="sec-rule abs" style="top:932px;background:var(--rule)"></div>

<article class="course abs" style="left:92px;top:985px">
  <h3>Reiki Level I, II &amp;<br>Master Certification</h3>
  <div class="course-img selected" role="img" aria-label="Photo of stacked stones on a beach at sunset" style="background:linear-gradient(#8fa7c7,#e9c89a 45%,#6f8ea8 60%,#b59473)"></div>
  <p>Learn about Reiki, a universal energy that has been used successfully all over....</p>
  <a class="more hi" href="#">Read More</a>
</article>
<article class="course abs" style="left:346px;top:985px">
  <h3>Animal Reiki<br>Practitioner Certification</h3>
  <div class="course-img" role="img" aria-label="Photo of a small white dog receiving hands-on healing" style="background:linear-gradient(#6d8fd0,#c7d3ea 55%,#f1efe9)"></div>
  <p>In this course you will learn how to use Animal Reiki; a simple, non-invasive..</p>
  <a class="more" href="#">Read More</a>
</article>
<article class="course abs" style="left:603px;top:985px">
  <h3>Acupressure and Reiki for<br>Anxiety and Depression</h3>
  <div class="course-img" role="img" aria-label="Photo of a green leaf resting in raked sand" style="background:radial-gradient(circle,#5f8a3a 0 14%,#d7cfc4 16%,#bfb3a5 100%)"></div>
  <p>Do you feel down more often than up? Or do you find fear is preventing you...</p>
  <a class="more" href="#">Read More</a>
</article>
<article class="course abs" style="left:863px;top:985px">
  <h3>Your Soul is Calling<br>Creating Your Ideal Life</h3>
  <div class="course-img" role="img" aria-label="Abstract pink and white swirling light" style="background:radial-gradient(circle at 55% 45%,#f6eef3,#d79ac0 45%,#a8477f)"></div>
  <p>What would it be like to live the life you were meant to live? To have the world around you in...</p>
  <a class="more" href="#">Read More</a>
</article>

<section class="welcome abs" role="img" aria-label="Dark teal background with a faint white lotus and sparkles">
  <h2 class="sec-title abs" style="left:0;top:53px">Welcome to Bright Fern <em>Studies</em></h2>
  <div class="sec-rule abs" style="top:106px"></div>
  <p>Thought to be centuries old and rediscovered in the late 1800's, Reiki (pronounced ray-key) is a healing and enlightenment system. reikihealing Reiki can be translated into "Universal (Rei) Life Energy (Ki)". As a practitioner of Reiki, you attune your awareness to this energy and utilize it for the physical and emotional healing of self and others. Reiki is non-denominational and can be practiced by everyone, regardless of their religious and spiritual beliefs. Reiki can be performed hands-on in person or from a distance.</p>
  <a class="btn-dark abs" href="#">Read More</a>
  <div class="feature abs" style="left:184px"><div class="ico"><span></span></div>How<br>Reiki Works</div>
  <div class="feature abs" style="left:480px"><div class="ico"><span></span></div>Traditional Usui Reiki<br>Master Certification</div>
  <div class="feature abs" style="left:775px"><div class="ico"><span></span></div>Our<br>Resources</div>
</section>

<h2 class="col-title abs" style="left:100px;top:1850px">Latest <em>Blog Posts</em></h2>
<span class="arrows abs" style="left:540px;top:1862px">&lsaquo;&rsaquo;</span>
<div class="dotrule abs" style="left:100px;top:1895px;width:465px"></div>

<article class="post abs" style="top:1912px">
  <div class="post-img" role="img" aria-label="Photo of a person relaxing during a healing session" style="background:linear-gradient(135deg,#c9d7e4,#e9d6c8 60%,#9eb4c8)"></div>
  <div><h4>Ut tellus dolor, dapibus smit dollar nomk egemop dol</h4><div class="date">11.10.2016</div><p>Utm tellus dolor, dapibus eget, elemen velmki cursu itas.<br>Aenean auctorbni wisi et umam. Aliquam attpatiseleme<br>velmki cursu itas. Aenean auctorbni <b>[...]</b></p></div>
</article>
<div class="abs" style="left:100px;top:2015px;width:400px;height:1px;background:#ddd"></div>
<article class="post abs" style="top:2028px">
  <div class="post-img" role="img" aria-label="Photo of open hands holding warm light" style="background:radial-gradient(circle,#fff5e0,#f0a878 45%,#8fb0d8)"></div>
  <div><h4>Ut tellus dolor, dapibus smit dollar nomk egemop dol</h4><div class="date">11.10.2016</div><p>Utm tellus dolor, dapibus eget, elemen velmki cursu itas.<br>Aenean auctorbni wisi et umam. Aliquam attpatiseleme<br>velmki cursu itas. Aenean auctorbni <b>[...]</b></p></div>
</article>

<div class="abs" style="left:613px;top:1850px;width:1px;height:295px;background:#ddd"></div>

<h2 class="col-title abs" style="left:654px;top:1850px">Client <em>Testimonials</em></h2>
<span class="arrows abs" style="left:1080px;top:1862px">&lsaquo;&rsaquo;</span>
<div class="dotrule abs" style="left:654px;top:1895px;width:450px"></div>
<div class="avatar abs" role="img" aria-label="Client portrait"></div>
<div class="t-name abs">Mr. Quis Nostrud Exerci</div>
<div class="t-role abs">Business Man</div>
<p class="quote abs">Utm tellus dolor, dapibus eget, elemen velmki cursus eleifelita inean auctorbni wisi et umam. Lorem ipsum dolor sit amet, conse ctetur piscing elit. Nulla in sollicitudin velit, bibendum velit.Cras vel facilisis ipsum, etp venenatis risus. ipsum dolor sit amet, conse</p>

<footer class="site-footer abs" role="img" aria-label="Dark photo of stacked stones beside water">
  <nav class="foot-nav"><a class="active" href="#">Home</a><a href="#">About Us</a><a href="#">Online Courses</a><a href="#">Student Areas</a><a href="#">Testimonials</a><a href="#">Contact Us</a></nav>
  <div class="accept"><span>We Accept</span><i class="card" style="background:#2a4f9a"></i><i class="card" style="background:#e9e9e9"></i><i class="card" style="background:#1a3f95"></i><i class="card" style="background:#2f8fd0"></i><i class="card" style="background:#c8302a"></i></div>
  <div class="foot-brand"><span class="brand-dot"></span><span class="brand-name">BRIGHT FERN STUDIES</span></div>
  <p class="copy">Copyright © 2016 Bright Fern Studies. All Rights Reserved.</p>
</footer>

</body>
</html>
```